Judicial election website to attract voters

I need a simple one-page web design for a judicial election. I'm going to put up one picture, maybe two. The picture I have needs a little touch-up (whiten teeth for example). I have 3 paragraphs of text. I'd like a "Donate" button that can link to a CoinDrift account. I'd also like a little background design, like the Constitution or something like that. There's a couple other little things but that's the bulk of it.

Target Market(s)

Involved voters and some media

Industry/Entity Type

Legal

Number of Pages Required

1 page

Font styles to use
Sans Serif

Requirements
Must have
• My picture, text, donate button
• Phrase "Remember to vote August 30, 2016!"
Nice to have
• Perhaps a second photo, maybe a short 30 second video of me talking directly to the voters, cool background: Constitution, something judgey.
Should not have
• Not sure ... profanity, I guess.

```html
<!DOCTYPE html>
<html lang="en">
<head>
<meta charset="utf-8">
<title>Local Elections</title>
<link href="https://fonts.googleapis.com/css2?family=Lato:ital,wght@0,400;0,700;1,700&family=Questrial&display=swap" rel="stylesheet">
<style>
  :root {
    --navy: #23336b;
    --red: #c1272d;
    --red-soft: #b8343c;
    --ink: #333333;
    --page: #f1f1f1;
    --footer: #363636;
    --white: #ffffff;
  }
  * { box-sizing: border-box; margin: 0; padding: 0; }
  html, body { width: 1200px; height: 1128px; overflow: hidden; }
  body {
    background: var(--page);
    font-family: "Lato", sans-serif;
    color: var(--ink);
    position: relative;
  }
  .footer-band {
    position: absolute; left: 0; top: 1034px; width: 1200px; height: 94px;
    background: var(--footer);
  }
  .footer-band p {
    position: absolute; top: 52px; width: 100%; text-align: center;
    color: #f0f0f0; font-size: 14px;
  }
  .page {
    position: absolute; left: 171px; top: 0; width: 858px; height: 1063px;
    background: var(--white);
    box-shadow: 0 0 8px rgba(0,0,0,0.12);
  }
  .site-header { height: 50px; position: relative; }
  .brand {
    position: absolute; left: 18px; top: 12px;
    font-size: 23px; font-weight: 700; letter-spacing: 0.5px;
  }
  .brand .local { color: var(--navy); }
  .brand .elections { color: var(--red); }
  .follow {
    position: absolute; right: 18px; top: 10px; display: flex; align-items: center; gap: 8px;
  }
  .follow span { font-weight: 700; font-size: 17px; letter-spacing: 0.5px; margin-right: 8px; color: #222; }
  .social { width: 29px; height: 29px; border-radius: 50%; }
  .social.one { background: #3b5998; }
  .social.two { background: #1d9fd8; }

  .hero {
    position: absolute; top: 50px; left: 0; width: 858px; height: 428px;
    background: linear-gradient(100deg, #d9d6cc 0%, #cfc9bb 30%, #8a6a52 55%, #6b4a34 80%, #5a3c2a 100%);
  }
  .hero-arrow { position: absolute; top: 170px; }
  .hero-arrow.prev { left: 26px; }
  .hero-arrow.next { right: 26px; }
  .hero-copy {
    position: absolute; right: 86px; top: 298px; text-align: right;
    font-family: "Questrial", sans-serif; font-weight: 400;
  }
  .hero-copy .line1 { font-size: 35px; color: var(--white); text-shadow: 0 1px 3px rgba(0,0,0,0.5); font-weight: 700; }
  .hero-copy .line2 { font-size: 35px; color: var(--red); font-weight: 700; margin-top: 4px;
    text-shadow: 1px 0 0 #fff, -1px 0 0 #fff, 0 1px 0 #fff, 0 -1px 0 #fff; }

  .candidate-frame {
    position: absolute; left: 26px; top: 521px; width: 186px; height: 220px;
    border: 2px solid #333; padding: 4px; background: var(--white);
  }
  .candidate-photo {
    width: 100%; height: 100%;
    background: linear-gradient(160deg, #5a6fa8 0%, #c9b6a8 45%, #e8a585 100%);
  }
  .bio { position: absolute; left: 238px; top: 528px; width: 590px; }
  .bio p { font-size: 13.3px; line-height: 20.6px; margin-bottom: 12.3px; }

  .video {
    position: absolute; left: 18px; top: 784px; width: 394px; height: 233px;
    background: linear-gradient(135deg, #c8cfe0 0%, #aeb8d2 50%, #b85a55 100%);
  }
  .video .big-play { position: absolute; left: 167px; top: 69px; }
  .video-controls {
    position: absolute; left: 0; bottom: 0; width: 100%; height: 39px;
    background: #2c2f35; display: flex; align-items: center;
  }
  .video-controls .btn { width: 40px; height: 39px; border-right: 1px solid #1c1e22; display: flex; align-items: center; justify-content: center; }
  .progress { margin-left: 10px; width: 214px; height: 9px; border-radius: 5px; background: #15171a; position: relative; }
  .progress .buffered { position: absolute; left: 1px; top: 1px; height: 7px; width: 131px; background: #3d4148; border-radius: 4px; }
  .progress .played { position: absolute; left: 1px; top: 1px; height: 7px; width: 100px; background: linear-gradient(#3aa0e8, #1a6fc0); border-radius: 4px; }

  .support {
    position: absolute; left: 446px; top: 784px; width: 394px; height: 234px;
    background: radial-gradient(circle at 55% 55%, #6a6a6a 0%, #3d3d3d 60%, #2e2e2e 100%);
    text-align: center;
  }
  .support h2 {
    height: 43px; line-height: 45px; background: var(--red-soft);
    color: var(--white); font-size: 23px; font-weight: 700; letter-spacing: 1px;
  }
  .support .lead { margin-top: 20px; color: var(--white); font-style: italic; font-weight: 700; font-size: 17px; line-height: 26px; }
  .donate {
    display: inline-flex; margin-top: 12px; height: 35px; align-items: stretch;
    background: var(--red); color: var(--white); font-weight: 700; font-size: 16px; letter-spacing: 0.6px;
  }
  .donate .icon { width: 40px; background: #9e1f24; display: flex; align-items: center; justify-content: center; }
  .donate .label { padding: 0 13px 0 10px; line-height: 36px; }
  .pay-name { margin-top: 14px; color: var(--white); font-weight: 700; font-size: 21px; }
</style>
</head>
<body>
  <div class="footer-band"><p>Copyright © 2016 LOCAL ELECTIONS. &nbsp;All Rights Reserved</p></div>

  <main class="page">
    <header class="site-header">
      <div class="brand"><span class="local">LOCAL</span> <span class="elections">ELECTIONS</span></div>
      <div class="follow">
        <span>FOLLOW US :</span>
        <div class="social one" role="img" aria-label="Social page"></div>
        <div class="social two" role="img" aria-label="Social feed"></div>
      </div>
    </header>

    <section class="hero" role="img" aria-label="Voting booths with a flag and VOTE sign, voter in background">
      <svg class="hero-arrow prev" width="24" height="90" viewBox="0 0 24 90"><polyline points="20,2 3,45 20,88" fill="none" stroke="#fff" stroke-width="2"/></svg>
      <svg class="hero-arrow next" width="24" height="90" viewBox="0 0 24 90"><polyline points="4,2 21,45 4,88" fill="none" stroke="#fff" stroke-width="2"/></svg>
      <div class="hero-copy">
        <div class="line1">Remember to vote</div>
        <div class="line2">August 30, 2016!</div>
      </div>
    </section>

    <div class="candidate-frame">
      <div class="candidate-photo" role="img" aria-label="Portrait of the candidate in front of a flag"></div>
    </div>

    <section class="bio">
      <p>Lorem ipsum dolor sit amet, consectetur adipiscing elit. Sed vitae magna tellus. Aenean ante nunc, semper nec cursus non, rutrum ac eros. Vestibulum mattis justo ac dui bibendum consequat a ac ipsum. Praesent a arcu venenatis, auctor velit eu, suscipit libero.</p>
      <p>Lorem ipsum dolor sit amet, consectetur adipiscing elit. Sed vitae magna tellus. Aenean ante nunc, semper nec cursus non, rutrum ac eros. Vestibulum mattis justo ac dui bibendum consequat a ac ipsum. Praesent a arcu venenatis, auctor velit eu, suscipit libero.</p>
      <p>Lorem ipsum dolor sit amet, consectetur adipiscing elit. Sed vitae magna tellus. Aenean ante nunc, semper nec cursus non, rutrum ac eros. Vestibulum mattis justo ac dui bibendum consequat a ac ipsum. Praesent a arcu venenatis, auctor velit eu, suscipit libero.</p>
    </section>

    <section class="video" role="img" aria-label="Video: hand touching an electronic election ballot">
      <svg class="big-play" width="60" height="60" viewBox="0 0 60 60"><circle cx="30" cy="30" r="30" fill="#3a3d45" opacity="0.85"/><polygon points="24,18 24,42 43,30" fill="#fff"/></svg>
      <div class="video-controls">
        <div class="btn"><svg width="12" height="14" viewBox="0 0 12 14"><polygon points="0,0 0,14 12,7" fill="#fff"/></svg></div>
        <svg style="margin-left:10px" width="18" height="14" viewBox="0 0 18 14"><polygon points="0,4 4,4 9,0 9,14 4,10 0,10" fill="#fff"/><path d="M12 4 Q14 7 12 10 M14.5 2 Q18 7 14.5 12" stroke="#fff" stroke-width="1.3" fill="none"/></svg>
        <div class="progress"><div class="buffered"></div><div class="played"></div></div>
      </div>
    </section>

    <section class="support" aria-label="Support the campaign">
      <h2>SUPPORT THE CAMPAIGN</h2>
      <p class="lead">Your contributions make this<br>campaign possible.</p>
      <div class="donate">
        <span class="icon"><svg width="26" height="16" viewBox="0 0 26 16"><rect x="1" y="4" width="5" height="9" fill="none" stroke="#fff" stroke-width="1.5"/><path d="M6 6 H16 Q19 6 19 8 H12 M6 12 H18 L24 8" fill="none" stroke="#fff" stroke-width="1.5"/></svg></span>
        <span class="label">DONATE NOW</span>
      </div>
      <div class="pay-name">CoinDrift</div>
    </section>
  </main>
</body>
</html>
```